Cat-products company needs smart, yet endearing, business card

We need a business card design for a new, but up-and-running, business based in Honolulu, Hawaii. The business is Purrnest Nook Co. Our first product is the most environmentally-friendly cat grass kit ever seen on the planet. Future products, currently in the R&D phase, will include a variety of exciting cat scratchers. We also do consulting work to help apartment-dwellers make their home more cat-friendly and, in the future, plan on doing full, custom installs of structure to create high walkways for cats.

Target Market(s)

Middle-aged, apartment-dwelling, middle-class workers who own 1 or more cats and who dote on them.

Industry/Entity Type

Pet Care

Contact Information for Business Card

A striking, professional, yet warm and friendly design is what we're after.

Font styles to use
Serif
Sans Serif
Other font styles liked:
• Comfortaa

Colors

Designer to choose colors to be used in the design.

Requirements
Must have
• The company logo: (see attachment)
• The company name: Purrnest Nook Co
• The web address: www.purrnestnookco.com
• Email: support@purrnestnookco.com
• Phone: +1 (808) 571 6023
• Update (Fri Jun 30 3017 7:45pm Hawaii Time) I would like, is possible, uploaded picture of the cat grass kit on the back of the card with some text along the lines of: Purrnest Nook Co - Maker Of The Leafiest Feline Sprout Set Yet
Nice to have
• A cat picture, cartoon, real or silhouette that illustrates cats in action and/or relaxing; ie using the apartment space to live, play and relax in and being well-contented.
• Most of the website is done in the font: Comfortaa. It might be nice to continue using this for brand consistency.
Should not have
• Hard-to-read fonts.

```html
<!DOCTYPE html>
<html lang="en">
<head>
<meta charset="utf-8">
<title>Purrnest Nook Co — Business Card</title>
<link rel="stylesheet" href="https://fonts.googleapis.com/css2?family=Jost:wght@400;500;600&display=swap">
<style>
  :root {
    --stage: #1d1d1f;
    --card-white: #ffffff;
    --brown: #5e3a34;
    --brown-deep: #4f2f2a;
    --gold: #f5b21b;
    --ink: #3b2a27;
    --soft-white: #f6eeea;
  }
  * { box-sizing: border-box; margin: 0; padding: 0; }
  html, body {
    width: 1200px; height: 1000px; overflow: hidden;
    background: var(--stage);
    font-family: "Jost", sans-serif;
  }
  .stage {
    position: relative; width: 1200px; height: 1000px;
    display: flex; flex-direction: column; align-items: center; justify-content: center; gap: 60px;
  }
  .card {
    position: relative; width: 700px; height: 400px;
    background: var(--card-white); border-radius: 28px; overflow: hidden;
    box-shadow: 0 18px 40px rgba(0,0,0,0.45);
  }
  .brand {
    display: flex; align-items: center; gap: 12px;
    font-weight: 600; color: var(--brown); letter-spacing: 0.3px;
  }
  .brand-dot { width: 22px; height: 22px; border-radius: 50%; background: var(--gold); flex: none; }
  .card-front .brand {
    position: absolute; left: 50%; top: 50%; transform: translate(-50%, -50%);
    font-size: 40px;
  }
  .card-back .wave { position: absolute; inset: 0; }
  .card-back .brand {
    position: absolute; left: 44px; top: 70px; font-size: 30px;
  }
  .address {
    position: absolute; left: 44px; top: 250px;
    color: var(--ink); font-size: 17px; line-height: 1.35;
  }
  .person {
    position: absolute; right: 54px; top: 78px; text-align: right; color: var(--soft-white);
  }
  .person-name { font-size: 32px; font-weight: 500; letter-spacing: 0.5px; }
  .person-role { font-size: 15px; margin-top: 2px; }
  .contact {
    position: absolute; right: 40px; top: 196px; list-style: none;
    color: var(--soft-white); font-size: 16px; text-align: right;
  }
  .contact li { display: flex; justify-content: flex-end; align-items: center; gap: 10px; line-height: 1.7; }
  .contact svg { width: 14px; height: 14px; flex: none; }
</style>
</head>
<body>
<main class="stage">
  <section class="card card-front">
    <div class="brand"><span class="brand-dot"></span>Purrnest Nook Co</div>
  </section>

  <section class="card card-back">
    <svg class="wave" viewBox="0 0 700 400" preserveAspectRatio="none" aria-hidden="true">
      <path fill="var(--gold)" d="M490 0 L700 0 L700 400 L0 400 L0 352 C230 350 320 290 360 160 C390 60 430 20 490 0 Z"/>
      <path fill="var(--card-white)" d="M505 0 L700 0 L700 400 L0 400 L0 362 C240 362 332 300 372 168 C402 68 445 22 505 0 Z"/>
      <path fill="var(--brown)" d="M520 0 L700 0 L700 400 L0 400 L0 372 C250 372 344 308 384 176 C414 76 460 24 520 0 Z"/>
    </svg>
    <div class="brand"><span class="brand-dot"></span>Purrnest Nook Co</div>
    <p class="address">Your Street Address<br>Honolulu 96813</p>
    <div class="person">
      <p class="person-name">Kainoa Reyes</p>
      <p class="person-role">Founder/CEO</p>
    </div>
    <ul class="contact">
      <li>+1 (808) 571 6023
        <svg viewBox="0 0 16 16"><path fill="var(--gold)" d="M3 1h3l1.5 4-2 1.2a9 9 0 0 0 4.3 4.3L11 8.5l4 1.5v3a2 2 0 0 1-2 2A12 12 0 0 1 1 3a2 2 0 0 1 2-2z"/></svg></li>
      <li>support@purrnestnookco.com
        <svg viewBox="0 0 16 16"><rect x="1" y="3" width="14" height="10" rx="1.5" fill="var(--gold)"/><path d="M1.5 4 8 9l6.5-5" stroke="var(--brown)" stroke-width="1.4" fill="none"/></svg></li>
      <li>www.purrnestnookco.com
        <svg viewBox="0 0 16 16"><circle cx="8" cy="8" r="7" fill="var(--gold)"/><path d="M1 8h14M8 1c-3 3-3 11 0 14M8 1c3 3 3 11 0 14" stroke="var(--brown)" stroke-width="1.1" fill="none"/></svg></li>
    </ul>
  </section>
</main>
</body>
</html>
```